Standardization and redesign of graphics for a non-fiction book

For a book project, 11 graphics need to be visually unified so that all the graphics in the book are in the same style. The graphics must be created from scratch. Just new colors aren't enough. Some of the existing graphics are by other authors who own the copyright. Accordingly, the new graphics must be truly new. This is especially true for the "2 S-curves" graphic.

Target Market(s)

Manager Furniture Industry

Industry/Entity Type

Möbel

Colors
0054AA
0677BA
7BADD7
CADEEF
E8F1F8

```html
<!DOCTYPE html>
<html lang="de">
<head>
<meta charset="utf-8">
<title>Megatrends und Geschäftsmodelle in der Möbelbranche</title>
<link href="https://fonts.googleapis.com/css2?family=Poppins:wght@400;500;600;700&display=swap" rel="stylesheet">
<style>
:root{
  --teal:#1fe0c8;
  --teal-light:#5ff0dc;
  --blue:#1565c0;
  --blue-deep:#0054aa;
  --blue-mid:#0677ba;
  --ink:#2f3b52;
  --title:#0a47b8;
  --grey-text:#555e6c;
  --band:#f1f3f5;
  --band-dark:#e6e9ec;
  --bg:#ffffff;
}
html,body{margin:0;padding:0;width:1200px;height:1200px;overflow:hidden;background:var(--bg);}
svg{display:block;font-family:'Poppins',sans-serif;}
.topbar{fill:var(--teal);}
.chart-title{font-weight:700;font-size:14.5px;fill:var(--title);}
.chart-sub{font-size:14px;fill:var(--grey-text);}
.row-label{font-size:8px;fill:var(--grey-text);text-anchor:end;}
.row-band{fill:var(--band);}
.col-band{fill:var(--band-dark);opacity:.6;}
.bar22{fill:url(#g22);}
.bar20{fill:url(#g20);}
.tag{fill:var(--ink);}
.tag-text{font-size:4px;fill:#fff;font-weight:600;text-anchor:middle;}
.dot{fill:var(--ink);}
.axis{font-size:7.5px;font-weight:600;fill:var(--ink);text-anchor:middle;}
.legend{font-size:7.5px;font-weight:600;fill:var(--ink);}
.tri-face{fill:#eef0f3;}
.tri-divider{stroke:#d8dbe0;stroke-width:3;}
.q{font-size:12.5px;font-weight:600;fill:var(--ink);text-anchor:middle;}
.node-teal{fill:var(--teal);}
.node-blue{fill:var(--blue);}
.node-label-dark{font-size:17px;font-weight:700;fill:#3e4a5c;text-anchor:middle;}
.node-label-light{font-size:17px;font-weight:700;fill:#fff;text-anchor:middle;}
.tri-text{font-size:16px;font-weight:700;fill:var(--ink);text-anchor:middle;}
.ring{fill:none;stroke:var(--ink);stroke-width:2;}
.core{fill:url(#gcore);filter:url(#soft);}
.core-text{font-size:17px;font-weight:700;fill:var(--ink);text-anchor:middle;}
.c-head-dark{font-size:6.4px;font-weight:700;fill:var(--ink);text-anchor:middle;}
.c-body-dark{font-size:4.8px;fill:var(--ink);text-anchor:middle;}
.c-head-light{font-size:6.4px;font-weight:700;fill:#fff;text-anchor:middle;}
.c-body-light{font-size:4.8px;fill:#fff;text-anchor:middle;}
.c-body-big{font-size:6.6px;fill:#fff;text-anchor:middle;}
.connector{stroke:var(--ink);stroke-width:5;}
.col-text-dark{font-size:13.5px;font-weight:700;fill:var(--ink);text-anchor:middle;}
.col-text-light{font-size:13.5px;font-weight:700;fill:#fff;text-anchor:middle;}
.chevron{fill:none;stroke:var(--ink);stroke-width:9;stroke-linejoin:miter;}
.market-text{font-size:17px;font-weight:700;fill:var(--ink);text-anchor:middle;}
</style>
</head>
<body>
<svg width="1200" height="1200" viewBox="0 0 1200 1200" xmlns="http://www.w3.org/2000/svg">
  <defs>
    <linearGradient id="g22" x1="0" x2="1"><stop offset="0" stop-color="#1fe0c8"/><stop offset="1" stop-color="#5ff0dc"/></linearGradient>
    <linearGradient id="g20" x1="0" x2="1"><stop offset="0" stop-color="#0054aa"/><stop offset="1" stop-color="#2a8ee0"/></linearGradient>
    <radialGradient id="gcore" cx=".45" cy=".4" r=".7"><stop offset="0" stop-color="#ffffff"/><stop offset="1" stop-color="#e4e6ea"/></radialGradient>
    <filter id="soft" x="-20%" y="-20%" width="140%" height="140%"><feDropShadow dx="0" dy="2" stdDeviation="3" flood-color="#000" flood-opacity=".12"/></filter>
  </defs>

  <rect class="topbar" x="390" y="0" width="420" height="34"/>

  <!-- Megatrend chart -->
  <g class="chart">
    <text class="chart-title" x="312" y="168" text-anchor="middle">Die relevanten Megatrends in der Möbelbranche</text>
    <text class="chart-sub" x="312" y="188" text-anchor="middle">Vergleich Erhebung 2020 vs 2022</text>

    <g class="bands">
      <rect class="row-band" x="186" y="208" width="354" height="352"/>
      <rect class="col-band" x="257" y="208" width="71" height="352"/>
      <rect class="col-band" x="398" y="208" width="71" height="352"/>
    </g>

    <g class="labels">
      <text class="row-label" x="177" y="219">Convenience</text>
      <text class="row-label" x="177" y="240">Vertikalisierung</text>
      <text class="row-label" x="177" y="260">Biotech</text>
      <text class="row-label" x="177" y="281">Sicherheit</text>
      <text class="row-label" x="177" y="302">Industrie 4.0</text>
      <text class="row-label" x="177" y="323">Mobilität</text>
      <text class="row-label" x="177" y="344">Deglobalisierung</text>
      <text class="row-label" x="177" y="364">New Geo-Politics</text>
      <text class="row-label" x="177" y="385">New Work</text>
      <text class="row-label" x="177" y="406">Globalisierung</text>
      <text class="row-label" x="177" y="427">Gesundheit</text>
      <text class="row-label" x="177" y="448">Technologie &amp; Innovation</text>
      <text class="row-label" x="177" y="468">Urbanisierung</text>
      <text class="row-label" x="177" y="489">Individualisierung</text>
      <text class="row-label" x="177" y="510">Diversity &amp; Inclusion</text>
      <text class="row-label" x="177" y="531">Nachhaltigkeit</text>
      <text class="row-label" x="177" y="552">Digitalisierung</text>
    </g>

    <g class="bars-2022">
      <rect class="bar22" x="186" y="210.5" width="3" height="5" rx="2.5"/>
      <rect class="bar22" x="186" y="231.5" width="14" height="5" rx="2.5"/>
      <rect class="bar22" x="186" y="251.5" width="28" height="5" rx="2.5"/>
      <rect class="bar22" x="186" y="272.5" width="42" height="5" rx="2.5"/>
      <rect class="bar22" x="186" y="293.5" width="99" height="5" rx="2.5"/>
      <rect class="bar22" x="186" y="314.5" width="14" height="5" rx="2.5"/>
      <rect class="bar22" x="186" y="335.5" width="99" height="5" rx="2.5"/>
      <rect class="bar22" x="186" y="355.5" width="28" height="5" rx="2.5"/>
      <rect class="bar22" x="186" y="376.5" width="71" height="5" rx="2.5"/>
      <rect class="bar22" x="186" y="397.5" width="42" height="5" rx="2.5"/>
      <rect class="bar22" x="186" y="418.5" width="71" height="5" rx="2.5"/>
      <rect class="bar22" x="186" y="439.5" width="57" height="5" rx="2.5"/>
      <rect class="bar22" x="186" y="459.5" width="85" height="5" rx="2.5"/>
      <rect class="bar22" x="186" y="480.5" width="71" height="5" rx="2.5"/>
      <rect class="bar22" x="186" y="501.5" width="142" height="5" rx="2.5"/>
      <rect class="bar22" x="186" y="522.5" width="198" height="5" rx="2.5"/>
      <rect class="bar22" x="186" y="543.5" width="283" height="5" rx="2.5"/>
    </g>
    <g class="bars-2020">
      <rect class="bar20" x="186" y="220" width="14" height="5" rx="2.5"/>
      <rect class="bar20" x="186" y="241" width="14" height="5" rx="2.5"/>
      <rect class="bar20" x="186" y="261" width="28" height="5" rx="2.5"/>
      <rect class="bar20" x="186" y="282" width="28" height="5" rx="2.5"/>
      <rect class="bar20" x="186" y="303" width="42" height="5" rx="2.5"/>
      <rect class="bar20" x="186" y="324" width="42" height="5" rx="2.5"/>
      <rect class="bar20" x="186" y="345" width="57" height="5" rx="2.5"/>
      <rect class="bar20" x="186" y="365" width="71" height="5" rx="2.5"/>
      <rect class="bar20" x="186" y="386" width="85" height="5" rx="2.5"/>
      <rect class="bar20" x="186" y="407" width="85" height="5" rx="2.5"/>
      <rect class="bar20" x="186" y="428" width="85" height="5" rx="2.5"/>
      <rect class="bar20" x="186" y="449" width="99" height="5" rx="2.5"/>
      <rect class="bar20" x="186" y="469" width="99" height="5" rx="2.5"/>
      <rect class="bar20" x="186" y="490" width="127" height="5" rx="2.5"/>
      <rect class="bar20" x="186" y="511" width="127" height="5" rx="2.5"/>
      <rect class="bar20" x="186" y="532" width="198" height="5" rx="2.5"/>
      <rect class="bar20" x="186" y="553" width="221" height="5" rx="2.5"/>
    </g>

    <g class="value-tags">
      <g transform="translate(190,213)"><circle class="dot" r="1.3"/><rect class="tag" x="8" y="-3" width="14" height="6" rx="1"/><text class="tag-text" x="15" y="1.5">0%</text></g>
      <g transform="translate(197,222.5)"><circle class="dot" r="1.3"/><rect class="tag" x="8" y="-3" width="14" height="6" rx="1"/><text class="tag-text" x="15" y="1.5">1%</text></g>
      <g transform="translate(197,234)"><circle class="dot" r="1.3"/><rect class="tag" x="8" y="-3" width="14" height="6" rx="1"/><text class="tag-text" x="15" y="1.5">1%</text></g>
      <g transform="translate(197,243.5)"><circle class="dot" r="1.3"/><rect class="tag" x="8" y="-3" width="14" height="6" rx="1"/><text class="tag-text" x="15" y="1.5">1%</text></g>
      <g transform="translate(211,254)"><circle class="dot" r="1.3"/><rect class="tag" x="8" y="-3" width="14" height="6" rx="1"/><text class="tag-text" x="15" y="1.5">2%</text></g>
      <g transform="translate(211,263.5)"><circle class="dot" r="1.3"/><rect class="tag" x="8" y="-3" width="14" height="6" rx="1"/><text class="tag-text" x="15" y="1.5">2%</text></g>
      <g transform="translate(225,275)"><circle class="dot" r="1.3"/><rect class="tag" x="8" y="-3" width="14" height="6" rx="1"/><text class="tag-text" x="15" y="1.5">3%</text></g>
      <g transform="translate(211,284.5)"><circle class="dot" r="1.3"/><rect class="tag" x="8" y="-3" width="14" height="6" rx="1"/><text class="tag-text" x="15" y="1.5">2%</text></g>
      <g transform="translate(282,296)"><circle class="dot" r="1.3"/><rect class="tag" x="8" y="-3" width="14" height="6" rx="1"/><text class="tag-text" x="15" y="1.5">7%</text></g>
      <g transform="translate(225,305.5)"><circle class="dot" r="1.3"/><rect class="tag" x="8" y="-3" width="14" height="6" rx="1"/><text class="tag-text" x="15" y="1.5">3%</text></g>
      <g transform="translate(197,317)"><circle class="dot" r="1.3"/><rect class="tag" x="8" y="-3" width="14" height="6" rx="1"/><text class="tag-text" x="15" y="1.5">1%</text></g>
      <g transform="translate(225,326.5)"><circle class="dot" r="1.3"/><rect class="tag" x="8" y="-3" width="14" height="6" rx="1"/><text class="tag-text" x="15" y="1.5">3%</text></g>
      <g transform="translate(282,338)"><circle class="dot" r="1.3"/><rect class="tag" x="8" y="-3" width="14" height="6" rx="1"/><text class="tag-text" x="15" y="1.5">7%</text></g>
      <g transform="translate(240,347.5)"><circle class="dot" r="1.3"/><rect class="tag" x="8" y="-3" width="14" height="6" rx="1"/><text class="tag-text" x="15" y="1.5">4%</text></g>
      <g transform="translate(211,358)"><circle class="dot" r="1.3"/><rect class="tag" x="8" y="-3" width="14" height="6" rx="1"/><text class="tag-text" x="15" y="1.5">2%</text></g>
      <g transform="translate(254,367.5)"><circle class="dot" r="1.3"/><rect class="tag" x="8" y="-3" width="14" height="6" rx="1"/><text class="tag-text" x="15" y="1.5">5%</text></g>
      <g transform="translate(254,379)"><circle class="dot" r="1.3"/><rect class="tag" x="8" y="-3" width="14" height="6" rx="1"/><text class="tag-text" x="15" y="1.5">5%</text></g>
      <g transform="translate(268,388.5)"><circle class="dot" r="1.3"/><rect class="tag" x="8" y="-3" width="14" height="6" rx="1"/><text class="tag-text" x="15" y="1.5">6%</text></g>
      <g transform="translate(225,400)"><circle class="dot" r="1.3"/><rect class="tag" x="8" y="-3" width="14" height="6" rx="1"/><text class="tag-text" x="15" y="1.5">3%</text></g>
      <g transform="translate(268,409.5)"><circle class="dot" r="1.3"/><rect class="tag" x="8" y="-3" width="14" height="6" rx="1"/><text class="tag-text" x="15" y="1.5">6%</text></g>
      <g transform="translate(254,421)"><circle class="dot" r="1.3"/><rect class="tag" x="8" y="-3" width="14" height="6" rx="1"/><text class="tag-text" x="15" y="1.5">5%</text></g>
      <g transform="translate(268,430.5)"><circle class="dot" r="1.3"/><rect class="tag" x="8" y="-3" width="14" height="6" rx="1"/><text class="tag-text" x="15" y="1.5">6%</text></g>
      <g transform="translate(240,442)"><circle class="dot" r="1.3"/><rect class="tag" x="8" y="-3" width="14" height="6" rx="1"/><text class="tag-text" x="15" y="1.5">4%</text></g>
      <g transform="translate(282,451.5)"><circle class="dot" r="1.3"/><rect class="tag" x="8" y="-3" width="14" height="6" rx="1"/><text class="tag-text" x="15" y="1.5">7%</text></g>
      <g transform="translate(268,462)"><circle class="dot" r="1.3"/><rect class="tag" x="8" y="-3" width="14" height="6" rx="1"/><text class="tag-text" x="15" y="1.5">6%</text></g>
      <g transform="translate(282,471.5)"><circle class="dot" r="1.3"/><rect class="tag" x="8" y="-3" width="14" height="6" rx="1"/><text class="tag-text" x="15" y="1.5">7%</text></g>
      <g transform="translate(254,483)"><circle class="dot" r="1.3"/><rect class="tag" x="8" y="-3" width="14" height="6" rx="1"/><text class="tag-text" x="15" y="1.5">5%</text></g>
      <g transform="translate(310,492.5)"><circle class="dot" r="1.3"/><rect class="tag" x="8" y="-3" width="14" height="6" rx="1"/><text class="tag-text" x="15" y="1.5">9%</text></g>
      <g transform="translate(325,504)"><circle class="dot" r="1.3"/><rect class="tag" x="8" y="-3" width="16" height="6" rx="1"/><text class="tag-text" x="16" y="1.5">10%</text></g>
      <g transform="translate(310,513.5)"><circle class="dot" r="1.3"/><rect class="tag" x="8" y="-3" width="14" height="6" rx="1"/><text class="tag-text" x="15" y="1.5">9%</text></g>
      <g transform="translate(381,525)"><circle class="dot" r="1.3"/><rect class="tag" x="8" y="-3" width="16" height="6" rx="1"/><text class="tag-text" x="16" y="1.5">14%</text></g>
      <g transform="translate(381,534.5)"><circle class="dot" r="1.3"/><rect class="tag" x="8" y="-3" width="16" height="6" rx="1"/><text class="tag-text" x="16" y="1.5">14%</text></g>
      <g transform="translate(466,546)"><circle class="dot" r="1.3"/><rect class="tag" x="8" y="-3" width="16" height="6" rx="1"/><text class="tag-text" x="16" y="1.5">20%</text></g>
      <g transform="translate(404,555.5)"><circle class="dot" r="1.3"/><rect class="tag" x="8" y="-3" width="16" height="6" rx="1"/><text class="tag-text" x="16" y="1.5">14%</text></g>
    </g>

    <g class="axis-labels">
      <text class="axis" x="192" y="574">0%</text>
      <text class="axis" x="254" y="574">5%</text>
      <text class="axis" x="326" y="574">10%</text>
      <text class="axis" x="396" y="574">15%</text>
      <text class="axis" x="467" y="574">20%</text>
      <text class="axis" x="538" y="574">25%</text>
    </g>
    <g class="legend-group">
      <rect class="bar22" x="262" y="598" width="22" height="6" rx="3"/>
      <text class="legend" x="287" y="604">2022</text>
      <rect class="bar20" x="315" y="598" width="22" height="6" rx="3"/>
      <text class="legend" x="340" y="604">2020</text>
    </g>
  </g>

  <!-- Business model triangle -->
  <g class="triangle">
    <polygon class="tri-face" points="850,266 666,539 1035,539"/>
    <line class="tri-divider" x1="850" y1="427" x2="758" y2="386"/>
    <line class="tri-divider" x1="850" y1="427" x2="943" y2="386"/>
    <line class="tri-divider" x1="850" y1="427" x2="850" y2="539"/>
    <text class="tri-text" x="850" y="349">Nutzenver-</text>
    <text class="tri-text" x="850" y="366">sprechen</text>
    <text class="tri-text" x="775" y="490">Ertrags-</text>
    <text class="tri-text" x="775" y="507">mechanik</text>
    <text class="tri-text" x="927" y="481">Wert-</text>
    <text class="tri-text" x="927" y="498">schöpfungs-</text>
    <text class="tri-text" x="927" y="515">kette</text>

    <circle class="node-teal" cx="850" cy="266" r="50"/>
    <text class="node-label-dark" x="850" y="273">Was?</text>
    <circle class="node-blue" cx="850" cy="427" r="50"/>
    <text class="node-label-light" x="850" y="434">Wer?</text>
    <circle class="node-teal" cx="666" cy="539" r="50"/>
    <text class="node-label-dark" x="666" y="546">Wert?</text>
    <circle class="node-teal" cx="1035" cy="539" r="50"/>
    <text class="node-label-dark" x="1035" y="546">Wie?</text>

    <text class="q" x="850" y="180">Was bieten wir dem</text>
    <text class="q" x="850" y="198">Kunden an?</text>
    <text class="q" x="634" y="460">Wie wird Wert</text>
    <text class="q" x="634" y="478">erzielt?</text>
    <text class="q" x="1066" y="460">Wie stellen wir die</text>
    <text class="q" x="1066" y="478">Leistung her?</text>
    <text class="q" x="850" y="567">Wer sind unsere</text>
    <text class="q" x="850" y="585">Zielkunden?</text>
  </g>

  <!-- Target customer ring -->
  <g class="customer-ring">
    <circle class="ring" cx="324" cy="874" r="156"/>
    <circle class="core" cx="324" cy="874" r="76"/>
    <text class="core-text" x="324" y="881">Zielkunde</text>

    <circle class="node-teal" cx="324" cy="725" r="54"/>
    <text class="c-head-dark" x="324" y="705">Leistungskonzept</text>
    <text class="c-body-dark" x="324" y="713">Angebotspalette:</text>
    <text class="c-body-dark" x="324" y="724">Wohnungseinrichtungsgegenst</text>
    <text class="c-body-dark" x="324" y="732">ände und damit verbundenen</text>
    <text class="c-body-dark" x="324" y="740">Dienstleistungen wie Beratung,</text>
    <text class="c-body-dark" x="324" y="748">Lieferung, Entsorgung,</text>
    <text class="c-body-dark" x="324" y="756">Reparatur, Ersatzteile, …</text>

    <circle class="node-blue" cx="451" cy="790" r="54"/>
    <text class="c-head-light" x="451" y="766">Kanäle</text>
    <text class="c-body-big" x="451" y="782">Kommunikations- und</text>
    <text class="c-body-big" x="451" y="792">Verkaufskanäle</text>
    <text class="c-body-big" x="451" y="802">(Single-, Multiple- und</text>
    <text class="c-body-big" x="451" y="812">Omni-Channel)POS-</text>
    <text class="c-body-big" x="451" y="822">Konzept</text>

    <circle class="node-teal" cx="451" cy="941" r="54"/>
    <text class="c-head-dark" x="451" y="915">Wertschöpfungskonzept</text>
    <text class="c-body-dark" x="451" y="924">vertikale Integration vs reiner</text>
    <text class="c-body-dark" x="451" y="931">Handel, Einkaufsstrategie</text>
    <text class="c-body-dark" x="451" y="938">(Global- oder Local-Sourcing,</text>
    <text class="c-body-dark" x="451" y="945">Lagerhaltung,</text>
    <text class="c-body-dark" x="451" y="952">Einzelstückfertigung,</text>
    <text class="c-body-dark" x="451" y="959">…)Innenarchitektur, komplexe</text>
    <text class="c-body-dark" x="451" y="966">Einrichtungsberatung, Farb- und</text>
    <text class="c-body-dark" x="451" y="973">Stylingkonzepte, …</text>

    <circle class="node-blue" cx="324" cy="1024" r="54"/>
    <text class="c-head-light" x="324" y="1005">Wertverteilung</text>
    <text class="c-body-light" x="324" y="1019">Shareholder-Konzept,</text>
    <text class="c-body-light" x="324" y="1027">Einbezug des Managements</text>
    <text class="c-body-light" x="324" y="1035">und der Mitarbeiter,</text>
    <text class="c-body-light" x="324" y="1043">Öffentlichkeitsinteresse</text>

    <circle class="node-teal" cx="197" cy="941" r="54"/>
    <text class="c-head-dark" x="197" y="922">Ertragsmodell</text>
    <text class="c-body-dark" x="197" y="936">margengetriebenes Modell</text>
    <text class="c-body-dark" x="197" y="944">(Verkaufspreise), Miete,</text>
    <text class="c-body-dark" x="197" y="952">Dienstleistungsgebühren</text>
    <text class="c-body-dark" x="197" y="960">(Living as a Service, Logistik,</text>
    <text class="c-body-dark" x="197" y="968">Reparatur)</text>

    <circle class="node-blue" cx="197" cy="790" r="54"/>
    <text class="c-head-light" x="197" y="768">Entwicklungskonzept</text>
    <text class="c-body-light" x="197" y="781">z.B. Open Innovation im</text>
    <text class="c-body-light" x="197" y="789">Rahmen eines 2-S-Kurven-</text>
    <text class="c-body-light" x="197" y="797">ModellsService- &amp;</text>
    <text class="c-body-light" x="197" y="805">ProduktentwicklungDigitalstr</text>
    <text class="c-body-light" x="197" y="813">ategie,</text>
    <text class="c-body-light" x="197" y="821">Nachhaltigkeitsstrategie</text>
  </g>

  <!-- Market drivers -->
  <g class="market-drivers">
    <line class="connector" x1="709" y1="780" x2="709" y2="820"/>
    <line class="connector" x1="735" y1="780" x2="735" y2="820"/>
    <line class="connector" x1="709" y1="926" x2="709" y2="966"/>
    <line class="connector" x1="735" y1="926" x2="735" y2="966"/>

    <circle class="node-teal" cx="722" cy="728" r="56"/>
    <text class="col-text-dark" x="722" y="719">makroöko-</text>
    <text class="col-text-dark" x="722" y="733">nomisches</text>
    <text class="col-text-dark" x="722" y="747">Umfeld</text>

    <circle class="node-blue" cx="722" cy="873" r="56"/>
    <text class="col-text-light" x="722" y="871">Mega-</text>
    <text class="col-text-light" x="722" y="885">trends</text>

    <circle class="node-teal" cx="722" cy="1018" r="56"/>
    <text class="col-text-dark" x="722" y="1008">neue</text>
    <text class="col-text-dark" x="722" y="1022">Geschäfts-</text>
    <text class="col-text-dark" x="722" y="1036">modelle</text>

    <polyline class="chevron" points="806,856 824,874 806,892"/>

    <circle class="core" cx="950" cy="874" r="96"/>
    <text class="market-text" x="950" y="861">Schweizer</text>
    <text class="market-text" x="950" y="879">Wohnungs-</text>
    <text class="market-text" x="950" y="897">einrichtungsmarkt*</text>
  </g>
</svg>
</body>
</html>
```